Interior Design Company - Project Folder Design

Require simple layout design for company folders in a specific template as attach. Company name is MORVEL. Tag line is "make each space your own story" in Microsoft Word <Juice ITC> font type. Corporate colors include dark grey, turqoise and white.
Logo, AI template and some images are attached.

Company focus on Interior Design and Build services. Our services includes all commercial and residential projects.

Target Market(s)

B2B,B2C Corporate and Residential Design, Fit-outs and Project Management

Industry/Entity Type

Interior

Font styles to use
Sans Serif

Colors
33a6d7
333333
ffffff

Requirements
Must have
• Logo
• Address - No. 58 Kelton Road #03-21, Varlow Plaza, Singapore 179452
• Web - www.morvel-example.com
Nice to have
• Clean professional architectural lines
Should not have
• No cartoons, kiddy images nor repetitive patterns

```html
<!DOCTYPE html>
<html lang="en">
<head>
<meta charset="utf-8">
<title>MORVEL – Quotation Folder</title>
<link rel="stylesheet" href="https://fonts.googleapis.com/css2?family=Quicksand:wght@300;500&family=Pompiere&family=Open+Sans:wght@400&display=swap">
<style>
  :root {
    --bg: #d8d8d8;
    --turquoise: #2ea6d9;
    --ink: #050505;
    --white: #ffffff;
    --dieline: #c0394b;
    --partner-blue: #1f3c99;
    --badge: #f08a12;
    --badge-deep: #d9700a;
    --muted: #b9b9b9;
  }
  * { margin: 0; padding: 0; box-sizing: border-box; }
  html, body { width: 1200px; height: 818px; overflow: hidden; background: var(--bg); }
  .canvas { position: relative; width: 1200px; height: 818px; }
  .folder-art { position: absolute; inset: 0; }
  .brand {
    position: absolute; font-family: "Quicksand", sans-serif; font-weight: 300;
    color: var(--white); letter-spacing: 1px; line-height: 1; white-space: nowrap;
  }
  .brand--front { left: 984px; top: 572px; font-size: 32px; }
  .brand--flap { left: 186px; top: 405px; font-size: 21px; }
  .brand--back { left: 310px; top: 609px; font-size: 15px; }
  .tagline {
    position: absolute; font-family: "Pompiere", sans-serif; color: var(--muted);
    white-space: nowrap; line-height: 1;
  }
  .tagline--front { left: 870px; top: 630px; font-size: 25px; }
  .tagline--flap {
    left: 30px; top: 366px; width: 210px; text-align: center;
    font-size: 18px; color: var(--ink);
    transform: rotate(-45deg); transform-origin: center;
  }
  .address {
    position: absolute; left: 310px; top: 638px; font-style: normal;
    font-family: "Open Sans", sans-serif; font-size: 7px; line-height: 9px; color: var(--muted);
  }
  .spine-label {
    position: absolute; font-family: "Open Sans", sans-serif; font-size: 5.5px;
    letter-spacing: 2.2px; color: var(--ink); white-space: nowrap;
    transform-origin: left top; transform: rotate(90deg);
  }
  .spine-label--top { left: 709px; top: 144px; }
  .spine-label--bottom { left: 709px; top: 600px; }
  .partner-name {
    position: absolute; left: 734px; top: 152px;
    font-family: "Quicksand", sans-serif; font-weight: 500; font-size: 26px;
    color: var(--partner-blue); line-height: 1; white-space: nowrap;
  }
</style>
</head>
<body>
<main class="canvas">
  <svg class="folder-art" width="1200" height="818" viewBox="0 0 1200 818">
    <defs>
      <linearGradient id="interior-tones" x1="0" y1="0.15" x2="1" y2="0.85">
        <stop offset="0" stop-color="#d9dbdc"/>
        <stop offset="0.22" stop-color="#9a9c9e"/>
        <stop offset="0.42" stop-color="#45423e"/>
        <stop offset="0.58" stop-color="#6e5f3a"/>
        <stop offset="0.74" stop-color="#caa04a"/>
        <stop offset="0.88" stop-color="#8a7a5a"/>
        <stop offset="1" stop-color="#2c2a28"/>
      </linearGradient>
      <radialGradient id="badge-fill" cx="0.45" cy="0.4" r="0.6">
        <stop offset="0" stop-color="var(--badge)"/>
        <stop offset="1" stop-color="var(--badge-deep)"/>
      </radialGradient>
    </defs>

    <!-- pocket flap -->
    <g class="pocket-flap">
      <rect x="67" y="83" width="215" height="651" fill="var(--turquoise)"/>
      <polygon points="67,474 206,336 282,412 282,734 67,734" fill="var(--ink)"/>
    </g>

    <!-- cover photo area -->
    <rect class="cover-photo" x="282" y="126" width="851" height="567" fill="url(#interior-tones)"
          role="img" aria-label="Rendered office interior with warmly lit bookshelves, a long desk and white chairs"/>

    <!-- architectural overlay facets -->
    <g class="cover-facets">
      <polygon points="400,196 698,508 400,520" fill="#000000" opacity="0.18"/>
      <polygon points="400,196 1072,140 698,508" fill="#ffffff" opacity="0.13"/>
      <polygon points="1072,140 1133,140 1133,400" fill="#000000" opacity="0.15"/>
      <line x1="400" y1="196" x2="698" y2="508" stroke="#ffffff" stroke-opacity="0.25" stroke-width="0.8"/>
      <line x1="1072" y1="140" x2="698" y2="508" stroke="#ffffff" stroke-opacity="0.25" stroke-width="0.8"/>
    </g>

    <!-- back cover corner -->
    <polygon class="back-corner" points="282,392 538,693 282,693" fill="var(--ink)"/>
    <!-- front cover corner -->
    <polygon class="front-corner" points="790,693 1037,470 1133,588 1133,693" fill="var(--ink)"/>

    <!-- partner badge -->
    <circle class="partner-badge" cx="1013" cy="406" r="54" fill="url(#badge-fill)"/>

    <!-- logo rule lines -->
    <line x1="980" y1="607" x2="1075" y2="607" stroke="var(--white)" stroke-width="0.8"/>
    <line x1="185" y1="430" x2="252" y2="430" stroke="var(--white)" stroke-width="0.6"/>

    <!-- dielines -->
    <g class="dielines" fill="none" stroke="var(--dieline)" stroke-width="0.7">
      <rect x="282" y="126" width="851" height="567"/>
      <line x1="701" y1="126" x2="701" y2="693"/>
      <line x1="708" y1="126" x2="708" y2="693"/>
      <line x1="267" y1="83" x2="267" y2="734"/>
      <line x1="67" y1="110" x2="267" y2="110"/>
      <line x1="67" y1="126" x2="267" y2="126"/>
      <line x1="67" y1="693" x2="267" y2="693"/>
      <line x1="67" y1="707" x2="267" y2="707"/>
      <line x1="67" y1="110" x2="77" y2="88"/>
      <line x1="267" y1="110" x2="257" y2="88"/>
      <line x1="67" y1="707" x2="77" y2="730"/>
      <line x1="267" y1="707" x2="257" y2="730"/>
      <path d="M85,582 Q100,607 85,633"/>
      <path d="M180,582 Q155,607 180,633"/>
      <path d="M252,582 Q230,607 252,633"/>
      <path d="M130,658 Q160,640 190,658"/>
    </g>
  </svg>

  <div class="partner-name">Kanzo Coatings</div>

  <span class="spine-label spine-label--top">Kanzo Coatings Preferred Designers</span>
  <span class="spine-label spine-label--bottom">Quotation Folder</span>

  <div class="brand brand--front">morvel</div>
  <div class="tagline tagline--front">make each space your own story</div>

  <div class="brand brand--flap">morvel</div>
  <div class="tagline tagline--flap">make each space your own story</div>

  <div class="brand brand--back">morvel</div>
  <address class="address">
    No. 58 Kelton Road #03-21,<br>
    Varlow Plaza, Singapore 179452<br>
    www.morvel-example.com
  </address>
</main>
</body>
</html>
```